BRELWINCare.co.uk - Mental Health Clinic for Child and Adolescents

Updated 29/01/2018***
I am not sure you guys are getting the idea regards to the opening page / homescreen layout. Can you look at the new images I have uploaded (page 5, 6 and 7) These are some of the layouts I like but to incorporate my chosen images, with the BRELWIN commissioner, buttons and a sliding header bar.
I have written a strong brief, I am looking for a website, preferably wordpress as i know they are easy to maintain. I am looking for a one page site, with the top / opening page being full screen image with drop down categories. I have made a rough design, see full brief in word doc attached, there is some freedom to play around with the design aspect but it will need to relay all the content provided. I like a minimal feel. I have also attached some images that may be useful, but will need a new logo for BRELWIN Care. I have attached some logo idea's, it is up to you decide whether you want to use them.
I would prefer the homepage as full screen image, and the categories offered as a drop down or over the main image.
I have also attached linked to some competitors websites:
https://www.vorimant-health.co.uk/
http://www.qlbn.org.uk/
Industry/Entity Type
Clinic
Number of Pages Required
1 page
Font styles to use
Look and feel
Each slider illustrates characteristics of the customer's brand and the style your logo design should communicate.

```html
<!DOCTYPE html>
<html lang="en">
<head>
<meta charset="utf-8">
<title>BRELWIN Care – Child &amp; Adolescent Mental Health Services</title>
<link href="https://fonts.googleapis.com/css2?family=Anton&family=Roboto:wght@400;500;700&display=swap" rel="stylesheet">
<style>
:root{
  --teal:#00a9c4;
  --yellow:#e8e300;
  --lime:#9bcb2f;
  --pink:#e6157f;
  --navy:#1b2a5e;
  --navy-deep:#17245a;
  --ink:#2b2b2b;
  --grey:#8a8a8a;
  --white:#ffffff;
}
*{box-sizing:border-box;margin:0;padding:0}
html,body{width:1200px;height:2228px;overflow:hidden;background:var(--white)}
body{font-family:"Roboto",Arial,sans-serif;color:var(--ink);position:relative}
.display{font-family:"Anton",Impact,sans-serif;font-weight:400}

/* hero */
.hero{position:absolute;left:0;top:0;width:1200px;height:655px}
.sidebar{position:absolute;left:0;top:0;width:258px;height:655px;background:var(--teal)}
.home-tile{height:141px;background:linear-gradient(#f2ee3a,var(--yellow));display:flex;align-items:center;justify-content:center}
.main-nav a{display:flex;align-items:center;height:64.25px;padding-left:74px;color:var(--white);font-size:17px;font-weight:500;text-decoration:none;border-bottom:2px solid var(--yellow)}
.main-nav a:last-child{border-bottom:0}
.hero-photo{position:absolute;left:258px;top:0;width:942px;height:655px;background:linear-gradient(100deg,#d9cbbf 0%,#efe9e2 40%,#f6f2ec 60%,#d8c9b6 100%)}
.hero-brand{position:absolute;left:520px;top:180px;display:flex;align-items:center;gap:14px}
.brand-dot{width:96px;height:96px;border-radius:50%;background:var(--yellow)}
.brand-name{font-family:"Roboto",Arial,sans-serif;font-weight:700;font-size:40px;color:var(--teal);line-height:1}
.brand-sub{font-size:15px;color:#444;line-height:1.2;margin-top:6px}
.hero-cta{position:absolute;top:359px;display:flex;align-items:center;justify-content:center;width:178px;height:45px;border-radius:23px;color:var(--white);font-size:19px;font-weight:500;box-shadow:0 3px 0 rgba(0,0,0,.12)}
.cta-partners{left:508px;background:var(--lime)}
.cta-commissioners{left:700px;background:var(--pink)}

/* slider band */
.slider-band{position:absolute;left:0;top:655px;width:1200px;height:99px;background:var(--yellow);display:flex;align-items:center;justify-content:center;box-shadow:0 18px 24px -10px rgba(0,0,0,.25)}
.slider-text{font-size:39px;color:var(--navy);letter-spacing:.3px}
.slider-arrow{position:absolute;top:35px}
.arrow-prev{left:161px}.arrow-next{left:1007px}

/* welcome */
.welcome{position:absolute;left:0;top:754px;width:1200px;height:434px;text-align:center}
.welcome h1{font-size:50px;color:var(--ink);margin-top:80px;letter-spacing:.5px}
.welcome p{width:710px;margin:22px auto 0;font-size:12.5px;line-height:32px;color:var(--grey)}
.btn-read{display:inline-flex;align-items:center;justify-content:center;width:179px;height:48px;margin-top:22px;border-radius:24px;background:var(--lime);color:var(--white);font-size:19px;font-weight:500;box-shadow:0 3px 0 rgba(0,0,0,.12)}

/* blog */
.blog{position:absolute;left:0;top:1188px;width:1200px;height:550px;background:var(--teal)}
.blog h2{text-align:center;color:var(--white);font-size:47px;margin-top:72px}
.blog-card{position:absolute;top:165px;width:324px;height:289px;border-radius:14px;padding:12px;box-shadow:0 8px 10px rgba(0,0,0,.2)}
.card-pink{left:98px;background:var(--pink)}
.card-lime{left:438px;background:var(--lime)}
.card-pink-2{left:778px;background:var(--pink)}
.card-photo{height:232px;border-radius:12px}
.photo-a{background:linear-gradient(135deg,#e9e6e2,#b9b0a8)}
.photo-b{background:linear-gradient(135deg,#ece6df,#c8b7a6)}
.photo-c{background:linear-gradient(135deg,#efe9e3,#c6b7a5)}
.card-date{position:absolute;top:12px;right:12px;padding:6px 10px;font-size:13px;font-weight:500;color:var(--white);display:flex;gap:6px;align-items:center}
.card-pink .card-date,.card-pink-2 .card-date{background:var(--pink)}
.card-lime .card-date{background:var(--lime)}
.card-title{display:flex;justify-content:space-between;align-items:center;height:45px;padding:0 6px;color:var(--white);font-size:14.5px;font-weight:500}

/* footer */
.site-footer{position:absolute;left:0;top:1738px;width:1200px;height:490px;background:var(--navy)}
.footer-brand{position:absolute;left:98px;top:90px;display:flex;align-items:center;gap:10px}
.footer-brand .brand-dot{width:70px;height:70px}
.footer-brand .brand-name{font-size:28px}
.footer-brand .brand-sub{color:#d9dff0;font-size:10px}
.footer-col h3{font-size:27px;color:var(--white);letter-spacing:.5px}
.contact{position:absolute;left:383px;top:84px}
.contact-list{list-style:none;margin-top:22px}
.contact-list li{display:flex;align-items:center;gap:20px;height:49px;color:var(--white);font-size:12px;line-height:22px}
.contact-list li:first-child{height:60px}
.icon-ring{width:36px;height:36px;border:1.5px solid #6c78a2;border-radius:50%;display:flex;align-items:center;justify-content:center;flex:none}
.join{position:absolute;left:711px;top:84px}
.join p{color:var(--white);font-size:12px;margin-top:30px}
.subscribe{display:flex;margin-top:20px;width:389px;height:43px;border-radius:22px;overflow:hidden}
.subscribe span{flex:1;background:var(--white);color:#aaa;font-size:13px;padding-left:25px;display:flex;align-items:center}
.subscribe b{width:126px;background:var(--yellow);color:var(--white);font-size:14px;font-weight:500;display:flex;align-items:center;justify-content:center}
.social{display:flex;gap:10px;margin-top:24px}
.social i{width:36px;height:36px;border-radius:50%}
.rule{position:absolute;left:98px;top:406px;width:1004px;height:1px;background:#4a5688}
.copyright{position:absolute;left:0;top:442px;width:1200px;text-align:center;color:var(--white);font-size:11.5px}
</style>
</head>
<body>

<header class="hero">
  <aside class="sidebar">
    <div class="home-tile">
      <svg width="64" height="56" viewBox="0 0 64 56"><path d="M32 2 2 28h9v26h16V38h10v16h16V28h9L32 2z" fill="#00a9c4"/></svg>
    </div>
    <nav class="main-nav">
      <a>About us</a><a>Our Team</a><a>Our Services</a><a>Contact us</a>
      <a>Partners</a><a>Commissioners</a><a>Blog</a><a>Forum</a>
    </nav>
  </aside>
  <div class="hero-photo" role="img" aria-label="A clinician talking with a young girl at a desk in a bright office"></div>
  <div class="hero-brand">
    <span class="brand-dot"></span>
    <div>
      <div class="brand-name">BRELWIN</div>
      <div class="brand-sub">Child &amp; Adolescent Mental<br>Health Services</div>
    </div>
  </div>
  <a class="hero-cta cta-partners">Partners</a>
  <a class="hero-cta cta-commissioners">Commissioners</a>
</header>

<section class="slider-band">
  <svg class="slider-arrow arrow-prev" width="32" height="32" viewBox="0 0 32 32"><circle cx="16" cy="16" r="14" fill="none" stroke="#fff" stroke-width="2"/><path d="M19 9l-7 7 7 7" fill="none" stroke="#fff" stroke-width="2.2"/></svg>
  <div class="slider-text display">ADHD and autism screening within 24 hours</div>
  <svg class="slider-arrow arrow-next" width="32" height="32" viewBox="0 0 32 32"><circle cx="16" cy="16" r="14" fill="none" stroke="#fff" stroke-width="2"/><path d="M13 9l7 7-7 7" fill="none" stroke="#fff" stroke-width="2.2"/></svg>
</section>

<section class="welcome">
  <h1 class="display">Welcome !</h1>
  <p>Sed ut perspiciatis unde omnis iste natus error sit voluptatem accusantium doloremque laudantium, totam rem aperiam, eaque ipsa quae ab illo inventore veritatis et quasi architecto beatae vitae dicta sunt explicabo. Nemo enim ipsam voluptatem quia voluptas sit aspernatur aut odit aut fugit, sed quia consequuntur magni dolores eos qui ratione voluptatem sum quia dolor sit amet, consectetur, adipisci velit, sed quia non numquam eius modi tempora incidunt..</p>
  <a class="btn-read">Read More</a>
</section>

<section class="blog">
  <h2 class="display">Blog Posts</h2>
  <article class="blog-card card-pink">
    <div class="card-photo photo-a" role="img" aria-label="A group of teenagers sitting together on a sofa"></div>
    <span class="card-date"><svg width="12" height="12" viewBox="0 0 12 12"><rect x="1" y="2" width="10" height="9" fill="none" stroke="#fff"/><path d="M1 5h10" stroke="#fff"/></svg>NOV 2017</span>
    <div class="card-title">QUIS NOSTRUD EXERCITATIO<svg width="14" height="14" viewBox="0 0 14 14"><circle cx="7" cy="7" r="7" fill="#fff"/><path d="M5 4l3 3-3 3" fill="none" stroke="#e6157f" stroke-width="1.8"/></svg></div>
  </article>
  <article class="blog-card card-lime">
    <div class="card-photo photo-b" role="img" aria-label="A counsellor taking notes while talking with a young girl"></div>
    <span class="card-date"><svg width="12" height="12" viewBox="0 0 12 12"><rect x="1" y="2" width="10" height="9" fill="none" stroke="#fff"/><path d="M1 5h10" stroke="#fff"/></svg>NOV 2017</span>
    <div class="card-title">QUIS NOSTRUD EXERCITATIO<svg width="14" height="14" viewBox="0 0 14 14"><circle cx="7" cy="7" r="7" fill="#fff"/><path d="M5 4l3 3-3 3" fill="none" stroke="#9bcb2f" stroke-width="1.8"/></svg></div>
  </article>
  <article class="blog-card card-pink-2">
    <div class="card-photo photo-c" role="img" aria-label="A therapist working through papers with a young boy in a living room"></div>
    <span class="card-date"><svg width="12" height="12" viewBox="0 0 12 12"><rect x="1" y="2" width="10" height="9" fill="none" stroke="#fff"/><path d="M1 5h10" stroke="#fff"/></svg>NOV 2017</span>
    <div class="card-title">QUIS NOSTRUD EXERCITATIO<svg width="14" height="14" viewBox="0 0 14 14"><circle cx="7" cy="7" r="7" fill="#fff"/><path d="M5 4l3 3-3 3" fill="none" stroke="#e6157f" stroke-width="1.8"/></svg></div>
  </article>
</section>

<footer class="site-footer">
  <div class="footer-brand">
    <span class="brand-dot"></span>
    <div>
      <div class="brand-name">BRELWIN</div>
      <div class="brand-sub">Child &amp; Adolescent Mental<br>Health Services</div>
    </div>
  </div>

  <div class="footer-col contact">
    <h3 class="display">CONTACT US</h3>
    <ul class="contact-list">
      <li><span class="icon-ring"><svg width="12" height="16" viewBox="0 0 12 16"><path d="M6 0a6 6 0 0 0-6 6c0 4.5 6 10 6 10s6-5.5 6-10a6 6 0 0 0-6-6zm0 8.5A2.5 2.5 0 1 1 6 3.5a2.5 2.5 0 0 1 0 5z" fill="#fff"/></svg></span>Harlow Suite 4B, 12-20 Linden Road,<br>London, E99 7ZZ</li>
      <li><span class="icon-ring"><svg width="14" height="14" viewBox="0 0 14 14"><path d="M3 0l3 3-1.6 2a8 8 0 0 0 4.6 4.6L11 8l3 3-2 2.6C5.5 13 1 8.5.4 2z" fill="#fff"/></svg></span>Phone : 0200 000 0123</li>
      <li><span class="icon-ring"><svg width="16" height="16" viewBox="0 0 16 16"><circle cx="8" cy="8" r="7" fill="none" stroke="#fff" stroke-width="2"/><path d="M8 4v4l3 2" fill="none" stroke="#fff" stroke-width="1.8"/></svg></span>Hours : 9am – 5pm Mon-Fri</li>
      <li><span class="icon-ring"><svg width="16" height="12" viewBox="0 0 16 12"><rect width="16" height="12" rx="1.5" fill="#fff"/><path d="M0 1l8 6 8-6" fill="none" stroke="#1b2a5e" stroke-width="1.4"/></svg></span>Email – enquiry@brelwincare.co.uk</li>
    </ul>
  </div>

  <div class="footer-col join">
    <h3 class="display">JOIN US !</h3>
    <p>Sed ut perspiciatis unde omnis iste naem accusantium</p>
    <div class="subscribe"><span>Enter Email</span><b>SUBSCRIBE</b></div>
    <div class="social" aria-label="Social links">
      <i style="background:#3b5998"></i><i style="background:#1da1f2"></i><i style="background:#e52d27"></i><i style="background:#0e76a8"></i><i style="background:#dd4b39"></i>
    </div>
  </div>

  <div class="rule"></div>
  <div class="copyright">Copyrights © 2018 BRELWIN Care. All rights reserved.Privacy policy</div>
</footer>

</body>
</html>
```